Brightway Haul & Upkeep Services, are a company that offers a 'one stop shop' pre-move clean up a

I have already selected a logo which I would like on the front of the business cards along with phone numbers, web address and email which are:
0487650392
www.brightwayhaul.com.au
brightwayhaulandupkeep@mailbox.example

On the back of the card I would like to list some of the types of service we offer (clean - move - repairs/maintenance) which are:
CLEAN - windows, gutters, solar panels, driveways/paths, carpets.
MOVE - Small/medium size house/office moves, large item pick-up & delivery, yard clean-up and removal.
General maintenance and repairs.

I would like the blue logo on a gray background.

Thanks

```html
<!DOCTYPE html>
<html lang="en">
<head>
<meta charset="utf-8">
<title>Brightway Haul & Upkeep Services – Business Cards</title>
<link href="https://fonts.googleapis.com/css2?family=Open+Sans:wght@400;600;700&display=swap" rel="stylesheet">
<style>
  :root {
    --backdrop: #e4e4e4;
    --card-gray: #c9c9c9;
    --card-gray-light: #d6d6d6;
    --card-black: #000000;
    --brand-blue: #1f6ab5;
    --sky-blue: #7cbde9;
    --ink: #2b2b2b;
    --white: #ffffff;
  }
  * { box-sizing: border-box; margin: 0; padding: 0; }
  html, body { width: 1200px; height: 715px; overflow: hidden; }
  body {
    background: var(--backdrop);
    font-family: "Open Sans", Arial, sans-serif;
    position: relative;
  }
  .card {
    position: absolute;
    width: 548px;
    height: 312px;
    overflow: hidden;
    box-shadow: 0 2px 6px rgba(0,0,0,.25);
  }
  .card--front-gray { left: 32px; top: 30px; background: linear-gradient(180deg, var(--card-gray-light), var(--card-gray)); }
  .card--front-black { left: 618px; top: 30px; background: var(--card-black); }
  .card--back { left: 363px; top: 367px; background: linear-gradient(180deg, var(--card-gray-light), var(--card-gray)); }

  .wave { position: absolute; left: 0; top: 0; width: 548px; height: 312px; }

  .brand-name {
    position: absolute;
    font-weight: 700;
    color: var(--brand-blue);
    line-height: 1.05;
  }
  .card--front-black .brand-name { color: var(--white); }
  .card--front-gray .brand-name,
  .card--front-black .brand-name { left: 38px; top: 58px; }
  .brand-name__main { display: block; font-size: 46px; letter-spacing: -0.5px; }
  .brand-name__sub { display: block; font-size: 22px; margin-top: 8px; }

  .phone {
    position: absolute; left: 48px; top: 218px;
    display: flex; align-items: center; gap: 8px;
    font-size: 20px; color: var(--ink);
  }
  .card--front-black .phone { color: var(--white); }
  .phone svg { width: 16px; height: 16px; }

  .web {
    position: absolute; right: 12px; top: 265px;
    font-size: 15px; color: var(--white);
  }
  .email {
    position: absolute; right: 12px; top: 289px;
    display: flex; align-items: center; gap: 5px;
    font-size: 12px; color: var(--white);
  }
  .email svg { width: 10px; height: 8px; }

  .card--back .brand-name {
    left: 0; right: 0; top: 26px; text-align: center;
  }
  .card--back .brand-name__main { font-size: 40px; }
  .card--back .brand-name__sub { font-size: 19px; margin-top: 6px; }

  .services-title {
    position: absolute; left: 0; right: 0; top: 159px;
    text-align: center; font-size: 22px; font-weight: 600;
    letter-spacing: 1.5px; color: var(--brand-blue);
  }
  .service {
    position: absolute; left: 34px; right: 20px;
    font-size: 13.5px; color: var(--ink); line-height: 1.45;
  }
  .service__label { color: var(--brand-blue); font-weight: 600; font-size: 15px; margin-right: 6px; }
  .service--clean { top: 200px; }
  .service--move { top: 229px; display: grid; grid-template-columns: auto 1fr; }
  .service--move .service__list { text-align: center; }
  .services-footer {
    position: absolute; left: 0; right: 0; top: 280px;
    text-align: center; font-size: 16px; font-weight: 600;
    letter-spacing: 1px; color: var(--brand-blue);
  }
</style>
</head>
<body>

<section class="card card--front-gray" aria-label="Business card front, gray">
  <svg class="wave" viewBox="0 0 548 312" aria-hidden="true">
    <path d="M0,282 C120,300 250,292 360,238 C430,203 490,180 548,178 L548,312 L0,312 Z" fill="var(--brand-blue)"/>
    <path d="M0,252 C90,270 200,296 310,292 C200,306 80,300 0,284 Z" fill="var(--sky-blue)"/>
    <path d="M0,286 C120,302 240,300 330,282 C230,312 110,314 0,300 Z" fill="var(--card-gray-light)"/>
    <path d="M48,266 C180,292 300,272 380,228 C450,190 500,172 548,168 L548,177 C490,180 440,200 382,236 C300,284 180,294 48,266 Z" fill="#1b1b1b"/>
  </svg>
  <h1 class="brand-name">
    <span class="brand-name__main">Brightway Haul</span>
    <span class="brand-name__sub">&amp; Upkeep Services</span>
  </h1>
  <p class="phone">
    <svg viewBox="0 0 16 16" aria-hidden="true"><circle cx="8" cy="8" r="7.2" fill="none" stroke="var(--brand-blue)" stroke-width="1.3"/><path d="M5.5,4 L7,5.8 L6.2,7 C6.8,8.3 7.7,9.2 9,9.8 L10.2,9 L12,10.5 L11,12 C7.5,11.6 4.4,8.5 4,5 Z" fill="var(--brand-blue)"/></svg>
    0487650392
  </p>
  <p class="web">www.brightwayhaul.com.au</p>
  <p class="email">
    <svg viewBox="0 0 10 8" aria-hidden="true"><rect x="0.5" y="0.5" width="9" height="7" fill="none" stroke="var(--white)"/><path d="M0.5,0.5 L5,4.5 L9.5,0.5" fill="none" stroke="var(--white)"/></svg>
    brightwayhaulandupkeep@mailbox.example
  </p>
</section>

<section class="card card--front-black" aria-label="Business card front, black">
  <svg class="wave" viewBox="0 0 548 312" aria-hidden="true">
    <path d="M0,262 C120,292 250,292 360,238 C430,203 490,180 548,178 L548,312 L0,312 Z" fill="var(--brand-blue)"/>
    <path d="M0,258 C90,282 200,300 320,288 C200,306 80,300 0,280 Z" fill="var(--sky-blue)"/>
    <path d="M0,284 C120,302 240,300 330,282 C230,312 110,314 0,300 Z" fill="var(--card-black)"/>
    <path d="M48,266 C180,292 300,272 380,228 C450,190 500,172 548,168 L548,177 C490,180 440,200 382,236 C300,284 180,294 48,266 Z" fill="var(--card-black)"/>
    <path d="M60,280 C200,300 300,280 390,238 C460,204 505,186 548,180 L548,184 C500,192 460,210 392,244 C300,290 200,304 60,280 Z" fill="var(--sky-blue)"/>
  </svg>
  <h1 class="brand-name">
    <span class="brand-name__main">Brightway Haul</span>
    <span class="brand-name__sub">&amp; Upkeep Services</span>
  </h1>
  <p class="phone">
    <svg viewBox="0 0 16 16" aria-hidden="true"><circle cx="8" cy="8" r="7.2" fill="none" stroke="var(--white)" stroke-width="1.3"/><path d="M5.5,4 L7,5.8 L6.2,7 C6.8,8.3 7.7,9.2 9,9.8 L10.2,9 L12,10.5 L11,12 C7.5,11.6 4.4,8.5 4,5 Z" fill="var(--white)"/></svg>
    0487650392
  </p>
  <p class="web">www.brightwayhaul.com.au</p>
  <p class="email">
    <svg viewBox="0 0 10 8" aria-hidden="true"><rect x="0.5" y="0.5" width="9" height="7" fill="none" stroke="var(--white)"/><path d="M0.5,0.5 L5,4.5 L9.5,0.5" fill="none" stroke="var(--white)"/></svg>
    brightwayhaulandupkeep@mailbox.example
  </p>
</section>

<section class="card card--back" aria-label="Business card back">
  <h2 class="brand-name">
    <span class="brand-name__main">Brightway Haul</span>
    <span class="brand-name__sub">&amp; Upkeep Services</span>
  </h2>
  <h3 class="services-title">Services we offer</h3>
  <p class="service service--clean"><span class="service__label">CLEAN:</span>Windows, Gutters, Solar Panels, Driveways/paths, Carpets.</p>
  <p class="service service--move"><span class="service__label">MOVE:</span><span class="service__list">Small/medium Size House/office Moves, Large Item Pick-up &amp; Delivery, Yard Clean-up And Removal.</span></p>
  <p class="services-footer">General maintenance and repairs.</p>
</section>

</body>
</html>
```